SOLVE Study flyer

I need help designing a flyer for a research study that will include brain imaging in adolescents. The info is in the attached document. The study is called the Sequoia Outlook Lantern Valley Echo (SOLVE) study. Ideally this would be returned as a document that I can edit in the future as we will have several new recruitment phases (different age groups, etc. I also would love to have a logo designed as part of this project, but I recognize that might be a separate design request.

```html
<!DOCTYPE html>
<html lang="en">
<head>
<meta charset="utf-8">
<title>SOLVE Study Flyer</title>
<link href="https://fonts.googleapis.com/css2?family=Inter:wght@300;400;500;600;700;800&display=swap" rel="stylesheet">
<style>
:root{
  --navy:#07143f;
  --purple:#4a2ea8;
  --lavender:#ece8f6;
  --teal:#16918f;
  --teal-soft:#72c2b3;
  --mint:#eef7f5;
  --ink:#14162b;
  --white:#ffffff;
  --title-white:#f1ecfb;
}
*{margin:0;padding:0;box-sizing:border-box}
html,body{width:927px;height:1200px;overflow:hidden;background:var(--white)}
body{font-family:"Inter",Arial,sans-serif;color:var(--ink)}
.flyer{position:relative;width:927px;height:1200px;overflow:hidden;background:var(--white)}
.bands{position:absolute;inset:0;width:927px;height:1200px}
.hero-photo{position:absolute;left:370px;top:0;width:557px;height:430px;
  background:radial-gradient(ellipse at 55% 30%,#5a4a3e 0%,#2b2a33 35%,rgba(7,20,63,0) 75%);}
.abs{position:absolute}
.tagline{left:46px;top:30px;font-size:20px;line-height:30px;font-weight:600;color:var(--teal-soft)}
.study-name{left:40px;top:98px;font-size:112px;line-height:112px;font-weight:500;color:var(--white);letter-spacing:1px}
.study-word{left:40px;top:215px;font-size:112px;line-height:112px;font-weight:300;color:var(--title-white);letter-spacing:1px}
.acronym{left:46px;top:340px;font-size:20px;line-height:31px;font-weight:600;color:var(--white)}
.acronym .initial{color:var(--teal-soft)}
.sponsor-line{left:512px;top:346px;font-size:19px;font-weight:600;color:var(--teal-soft)}
.section-title{font-size:31px;line-height:35px;font-weight:700;letter-spacing:-.3px}
.eligible-title{left:46px;top:548px;color:var(--purple)}
.involves-title{left:512px;top:548px;color:var(--teal)}
.item{position:absolute;width:400px;height:96px}
.item .badge{position:absolute;left:0;top:0;width:94px;height:94px;border-radius:50%}
.item .badge::after{content:"";position:absolute;left:8px;top:8px;width:78px;height:78px;border-radius:50%}
.item.eligibility .badge{background:var(--lavender)}
.item.eligibility .badge::after{background:var(--purple)}
.item.involvement .badge{background:var(--mint)}
.item.involvement .badge::after{background:var(--teal-soft)}
.item h3{position:absolute;left:110px;top:11px;font-size:18px;font-weight:600;letter-spacing:-.2px;white-space:nowrap}
.item p{position:absolute;left:110px;top:39px;width:300px;font-size:13.4px;line-height:19.3px;font-weight:400;color:#23253a}
.contact-head{left:538px;top:1061px;font-size:18px;font-weight:700;color:var(--white)}
.contact-sub{left:540px;top:1091px;font-size:16px;color:var(--white)}
.email-pill{left:540px;top:1128px;width:326px;height:48px;border-radius:24px;background:var(--teal);
  display:flex;align-items:center;justify-content:center;gap:10px;color:var(--white);font-size:18.5px;font-weight:500}
.brand{left:84px;top:1108px;display:flex;align-items:center;gap:14px;color:var(--white);font-size:25px;font-weight:500}
.brand .mark{width:40px;height:40px;background:var(--white)}
.code{left:902px;top:1176px;font-size:7px;color:var(--white)}
</style>
</head>
<body>
<div class="flyer">
  <svg class="bands" viewBox="0 0 927 1200" aria-hidden="true">
    <path d="M0,405 C150,482 260,512 340,510 C520,505 700,408 927,422 V0 H0Z" fill="#4a2ea8"/>
    <path d="M0,405 C150,466 260,492 340,490 C520,485 700,402 927,416 V0 H0Z" fill="#ffffff"/>
    <path d="M0,405 C150,460 260,480 340,478 C520,472 700,394 927,410 V0 H0Z" fill="#16918f"/>
    <path d="M0,403 C150,448 260,464 340,462 C520,456 700,385 927,426 V0 H0Z" fill="#07143f"/>
    <path d="M0,988 C200,1012 450,996 600,999 C750,1004 850,1030 927,1056 V1200 H0Z" fill="#4a2ea8"/>
    <path d="M0,991 C150,1038 300,1056 450,1046 C650,1030 800,1036 927,1056 V1200 H0Z" fill="#ffffff"/>
    <path d="M0,996 C150,1052 300,1072 450,1063 C650,1050 800,1045 927,1056 V1200 H0Z" fill="#16918f"/>
    <path d="M0,1004 C150,1068 300,1088 450,1081 C650,1068 800,1050 927,1058 V1200 H0Z" fill="#07143f"/>
  </svg>

  <div class="hero-photo" role="img" aria-label="Photo of a smiling teenage girl wearing a fleece-lined hood, lit by warm sunlight"></div>

  <div class="abs tagline">Help us understand how the<br>Adolescent Brain Develops.</div>
  <div class="abs study-name">SOLVE</div>
  <div class="abs study-word">STUDY</div>
  <div class="abs acronym"><span class="initial">S</span>equoia <span class="initial">O</span>utlook<br><span class="initial">L</span>antern <span class="initial">V</span>alley <span class="initial">E</span>cho</div>
  <div class="abs sponsor-line">A Ridgeline University Research Study</div>

  <h2 class="abs section-title eligible-title">IS YOUR CHILD<br>ELIGIBLE?</h2>
  <h2 class="abs section-title involves-title">STUDY PARTICIPATION<br>INVOLVES</h2>

  <div class="item eligibility" style="left:47px;top:640px">
    <div class="badge"></div>
    <h3>GIRLS AGES 10-17</h3>
    <p>We are seeking girls between the ages of 10 and 17.</p>
  </div>
  <div class="item eligibility" style="left:47px;top:763px">
    <div class="badge"></div>
    <h3>TEND TO WORRY OR OVERTHINK</h3>
    <p>Does your child often worry or overthink negative thoughts or emotions?</p>
  </div>
  <div class="item eligibility" style="left:47px;top:886px">
    <div class="badge"></div>
    <h3>NO CERTAIN DIAGNOSES</h3>
    <p>Your child has not been diagnosed with psychosis, learning problems, or autism,</p>
  </div>

  <div class="item involvement" style="left:512px;top:640px">
    <div class="badge"></div>
    <h3>ONE 1-HOUR INTERVIEW</h3>
    <p>Online or in-person where your child will discuss their thoughts and experiences.</p>
  </div>
  <div class="item involvement" style="left:512px;top:763px">
    <div class="badge"></div>
    <h3>ONLINE QUESTIONNAIRES</h3>
    <p>Parent and child will complete online questionnaires.</p>
  </div>
  <div class="item involvement" style="left:512px;top:886px">
    <div class="badge"></div>
    <h3>ONE 2-HOUR RESEARCH VISIT</h3>
    <p>Includes an MRI scan, questions about puberty stage, and a small hair sample to study puberty hormones</p>
  </div>

  <div class="abs brand"><span class="mark"></span>Ridgeline University</div>

  <div class="abs contact-head">INTERESTED IN PARTICIPATING?</div>
  <div class="abs contact-sub">Want more information? Please contact us!</div>
  <div class="abs email-pill">
    <svg width="20" height="15" viewBox="0 0 20 15" aria-hidden="true"><rect x="0" y="0" width="20" height="15" rx="2" fill="#ffffff"/><path d="M1,1.5 L10,8.5 L19,1.5" fill="none" stroke="#16918f" stroke-width="1.8"/></svg>
    <span>solvestudy@ridgeline.edu</span>
  </div>
  <div class="abs code">C25</div>
</div>
</body>
</html>
```